Create a memorable Web Design for real estate branding

we are a Minnepolis brokerage and boutique housing specialist with over 27 years of experience in the Global furnished housing industry, servicing the Greater Los Angeles area. Specializing in “warm environments” we offer a customized approach to satisfying our guests and client’s needs by offering a wide array of options in highly desirable areas. Additionally, Lantern Dwelling Partners offers assistance and expertise to home buyers, sellers and investors.

Industry/Entity Type

Real Estate

Number of Pages Required

1 page

Font styles to use
Serif
Sans Serif
Decorative

```html
<!DOCTYPE html>
<html lang="en">
<head>
<meta charset="utf-8">
<title>Lantern Dwelling Partners</title>
<link href="https://fonts.googleapis.com/css2?family=Cinzel:wght@400;700&family=Lato:ital,wght@0,400;0,700;1,400&family=Oswald:wght@400&display=swap" rel="stylesheet">
<style>
:root{
  --black:#000;
  --teal:#0faa8f;
  --lime:#9ccb3b;
  --lime-dark:#8cbb2e;
  --ink:#222;
  --panel:rgba(0,0,0,.72);
  --white:#fff;
  --rule:#6f8f2a;
}
*{margin:0;padding:0;box-sizing:border-box}
html,body{width:1200px;height:1112px;overflow:hidden;background:var(--black);font-family:"Lato",sans-serif}
.page{position:relative;width:1200px;height:1112px}
.header{position:absolute;top:0;left:0;width:1200px;height:104px;background:var(--black)}
.brand{position:absolute;left:131px;top:12px;color:var(--teal);font-family:"Cinzel",serif;font-weight:700;font-size:40px;line-height:44px}
.brand small{display:block;font-size:28px;font-weight:400;padding-left:136px;line-height:34px}
.search{position:absolute;left:676px;top:38px;width:216px;height:26px;background:#d9d9d9;border:1px solid #999;font-style:italic;font-size:13px;color:#555;padding:4px 7px}
.search svg{position:absolute;right:6px;top:4px}
.phone{position:absolute;left:911px;top:39px;color:var(--white);font-size:20px;font-weight:700;display:flex;align-items:center;gap:9px}
.nav{position:absolute;top:104px;left:0;width:1200px;height:46px;background:var(--teal)}
.nav a{position:absolute;top:0;height:46px;line-height:46px;color:var(--white);font-family:"Cinzel",serif;font-weight:700;font-size:17px;text-decoration:none;text-align:center;letter-spacing:.5px}
.nav a.active{background:var(--lime);color:#1e3a14}
.nav .sep{position:absolute;top:4px;width:1px;height:38px;background:#0b7e6a}
.hero{position:absolute;top:150px;left:0;width:1200px;height:618px;background:linear-gradient(180deg,#3e5170 0%,#66708a 30%,#8a7653 55%,#b38532 75%,#2a2418 100%)}
.tagline{position:absolute;top:215px;left:130px;width:940px;height:108px;background:linear-gradient(90deg,rgba(0,0,0,0),rgba(0,0,0,.55) 15%,rgba(0,0,0,.55) 85%,rgba(0,0,0,0));text-align:center;color:var(--white);font-family:"Oswald",sans-serif;font-size:29px;line-height:46px;padding-top:8px}
.card{position:absolute;top:426px;height:142px;background:var(--panel);color:var(--white);padding:10px 20px 0 22px}
.card h2{font-family:"Cinzel",serif;font-weight:700;font-size:22px;line-height:30px;display:flex;align-items:center;gap:9px;margin-bottom:8px;white-space:nowrap}
.card h2 svg{flex:none}
.card h2 em{font-style:normal;color:var(--lime)}
.card p,.card li{font-size:13.5px;line-height:18px}
.card ul{list-style:none}
.card li{padding-left:16px;position:relative;margin-bottom:3px;white-space:nowrap}
.card li:before{content:"➜";position:absolute;left:0;font-size:9px}
.more{position:absolute;right:33px;bottom:8px;color:var(--lime);font-weight:700;font-size:13px}
.c1{left:136px;width:300px;clip-path:polygon(0 0,100% 0,97% 100%,0 100%)}
.c2{left:450px;width:300px;padding-left:30px;clip-path:polygon(3% 0,100% 0,97% 100%,0 100%)}
.c3{left:764px;width:305px;padding-left:28px;clip-path:polygon(3% 0,100% 0,100% 100%,0 100%)}
.select{margin-top:10px;width:242px;height:32px;background:#e6e6e6;border-radius:3px;color:#333;font-style:italic;font-size:13px;line-height:32px;padding-left:10px;position:relative}
.select b{position:absolute;right:0;top:0;width:32px;height:32px;background:#cfcfcf;border-radius:0 3px 3px 0}
.band{position:absolute;top:768px;left:0;width:1200px;height:8px;background:#2a2a2a}
.footer{position:absolute;top:776px;left:0;width:1200px;height:298px;background:var(--lime);color:var(--ink)}
.col{position:absolute;top:20px}
.col h3{font-family:"Cinzel",serif;font-weight:700;font-size:16px;color:#2a4a1a;padding-bottom:12px;border-bottom:1px dashed var(--rule);margin-bottom:14px;white-space:nowrap}
.map{width:246px;height:104px;border:4px solid #333;background:linear-gradient(135deg,#d8d6cf,#bdbbb2)}
.line{display:flex;gap:10px;font-size:13.5px;line-height:18px;margin-top:12px;align-items:flex-start}
.links li{list-style:none;font-size:13.5px;height:37px;padding-left:14px;position:relative}
.links li:before{content:"";position:absolute;left:2px;top:5px;border:3px solid transparent;border-left:4px solid #444}
.news h4{font-size:13.5px;margin-bottom:3px}
.news p{font-size:12px;line-height:16px}
.news i{display:block;font-size:13px;margin:3px 0 12px 2px}
.news hr{border:0;border-top:1px dashed var(--rule);margin-bottom:14px}
.follow div{display:flex;align-items:center;gap:14px;font-size:14.5px;height:58px}
.follow span{width:30px;height:30px;background:#2d4f3e;border-radius:3px}
.vr{position:absolute;top:40px;width:1px;height:240px;background:var(--lime-dark)}
.copy{position:absolute;bottom:0;left:0;width:1200px;height:38px;line-height:38px;text-align:center;color:var(--white);font-size:14.5px}
</style>
</head>
<body>
<div class="page">
  <header class="header">
    <div class="brand">Lantern Dwelling<small>Partners</small></div>
    <div class="search">Search Here<svg width="16" height="16" viewBox="0 0 16 16"><circle cx="9" cy="6" r="4.5" fill="none" stroke="#333" stroke-width="1.6"/><line x1="6" y1="9.5" x2="2" y2="14" stroke="#333" stroke-width="2"/></svg></div>
    <div class="phone"><svg width="24" height="24" viewBox="0 0 24 24"><circle cx="12" cy="12" r="11" fill="none" stroke="#9ccb3b" stroke-width="1.6"/><path d="M8 6l2 3-1.5 1.5c1 2 2.5 3.5 4.5 4.5L14.5 13.5l3 2-1.5 2.5C11 17.5 6.5 13 6 8z" fill="#9ccb3b"/></svg>012-555-0147</div>
  </header>
  <nav class="nav">
    <a class="active" style="left:131px;width:102px">HOME</a>
    <a style="left:233px;width:138px">ABOUT US</a><i class="sep" style="left:371px"></i>
    <a style="left:372px;width:159px">PROPERTIES</a><i class="sep" style="left:531px"></i>
    <a style="left:532px;width:155px">RESOURCES</a><i class="sep" style="left:687px"></i><i class="sep" style="left:714px"></i>
    <a style="left:715px;width:181px">TESTIMONIALS</a><i class="sep" style="left:896px"></i>
    <a style="left:897px;width:175px">CONTACT US</a>
  </nav>
  <section class="hero" role="img" aria-label="Photo of a lit two-storey home with a timber pergola and garden at dusk">
    <div class="tagline">WE ARE A BROKERAGE &amp; BOUTIQUE HOUSING SPECIALIST<br>WITH OVER 27 YEARS OF EXPERIENCE IN GREATER LOS ANGELES AREA</div>
    <div class="card c1">
      <h2><svg width="36" height="30" viewBox="0 0 36 30"><circle cx="18" cy="8" r="6" fill="#9ccb3b"/><circle cx="7" cy="11" r="4.5" fill="#9ccb3b"/><circle cx="29" cy="11" r="4.5" fill="#9ccb3b"/><path d="M8 30c0-9 4-13 10-13s10 4 10 13zM0 28c0-6 3-10 7-10 2 0 3 1 3 1-2 3-3 6-3 9zM36 28c0-6-3-10-7-10-2 0-3 1-3 1 2 3 3 6 3 9z" fill="#9ccb3b"/></svg><span>ABOUT <em>US</em></span></h2>
      <p>Lorem ipsum dolor sit amet uer adipicingt elsed diam nonmy nibh euismod tiidnsdth ut laoreet dolore magna erat.</p>
      <div class="more">READ MORE »</div>
    </div>
    <div class="card c2">
      <h2><svg width="30" height="30" viewBox="0 0 30 30"><circle cx="15" cy="15" r="15" fill="#9ccb3b"/><text x="15" y="22" text-anchor="middle" font-family="Lato" font-weight="700" font-size="20" fill="#111">?</text></svg><span>WHY <em>CHOOSE US</em></span></h2>
      <ul><li>Lorem ipsum dolor sit amet adipicingt</li><li>Eiismod tempor incididu oreet doefi</li><li>Atsid enim aminim elsed diam</li></ul>
      <div class="more">READ MORE »</div>
    </div>
    <div class="card c3">
      <h2><svg width="38" height="30" viewBox="0 0 38 30"><path d="M2 14L14 3l12 11" fill="none" stroke="#9ccb3b" stroke-width="3"/><rect x="6" y="13" width="8" height="13" fill="#9ccb3b"/><circle cx="25" cy="18" r="6" fill="none" stroke="#fff" stroke-width="2.5"/><line x1="29" y1="22" x2="35" y2="28" stroke="#fff" stroke-width="3"/></svg><span>FIND YOUR <em>HOME</em></span></h2>
      <p>Lorem ipsum dolor sit amet uer adipicingt elsed diam nonmy nibh euismod tnsdth</p>
      <div class="select">Single Family Residential<b><svg width="32" height="32" viewBox="0 0 32 32"><path d="M10 13l6 6 6-6" fill="none" stroke="#222" stroke-width="2.5"/></svg></b></div>
    </div>
  </section>
  <div class="band"></div>
  <footer class="footer">
    <div class="col" style="left:131px;width:246px">
      <h3>CONTACT US</h3>
      <div class="map" role="img" aria-label="Street map of the office location"></div>
      <div class="line"><svg width="16" height="20" viewBox="0 0 16 20"><path d="M8 0a7 7 0 0 1 7 7c0 5-7 13-7 13S1 12 1 7a7 7 0 0 1 7-7z" fill="#333"/><circle cx="8" cy="7" r="2.5" fill="#9ccb3b"/></svg><span>Lorem ipsum dolor sit amet uer adipici elsed diam nonmy nibh-012345</span></div>
      <div class="line"><svg width="16" height="12" viewBox="0 0 16 12"><rect x="1" y="1" width="14" height="10" fill="none" stroke="#333" stroke-width="1.5"/><path d="M1 1l7 6 7-6" fill="none" stroke="#333" stroke-width="1.5"/></svg><span>hello@lanterndwelling.example</span></div>
      <div class="line"><svg width="18" height="18" viewBox="0 0 24 24"><circle cx="12" cy="12" r="11" fill="none" stroke="#333" stroke-width="1.6"/><path d="M8 6l2 3-1.5 1.5c1 2 2.5 3.5 4.5 4.5L14.5 13.5l3 2-1.5 2.5C11 17.5 6.5 13 6 8z" fill="#333"/></svg><span>012-555-0147</span></div>
    </div>
    <i class="vr" style="left:422px"></i>
    <div class="col links" style="left:465px;width:112px">
      <h3>QUICK LINKS</h3>
      <ul><li>Home</li><li>About Us</li><li>Properties</li><li>Resources</li><li>Testimonials</li><li>Contacts Us</li></ul>
    </div>
    <i class="vr" style="left:620px"></i>
    <div class="col news" style="left:658px;width:201px">
      <h3>LATEST NEWS</h3>
      <h4>Lorem ipsum elsed diam</h4><p>Lorem ipsum dolor sit amet uer adipicingt elsed diam nonmy lorem elsed diam nonmy</p><i>06-June-2014</i>
      <hr>
      <h4>Lorem ipsum elsed diam</h4><p>Lorem ipsum dolor sit amet uer adipicingt elsed diam nonmy lorem elsed diam nonmy</p><i>06-June-2014</i>
    </div>
    <i class="vr" style="left:902px"></i>
    <div class="col follow" style="left:939px;width:128px">
      <h3>FOLLOW US</h3>
      <div><span></span>Community</div>
      <div><span></span>Updates</div>
      <div><span></span>Network</div>
      <div><span></span>Circles</div>
    </div>
  </footer>
  <div class="copy">Copyright © 2016 Lantern Dwelling Partners | All Rights Reserved.</div>
</div>
</body>
</html>
```